Clean business card with logo provided

I want a card that will stand out among the masses. I need the color and image to show professionalism and yet have a family appeal showing that I only deal with win/win scenarios. The back of the card will be used to take notes about the individual so I can use that in my database entry. I like modern design but need professionalism in it also. It needs to fit my "clean, safe, and affordable housing" motto. I need to be able to write on the file and update the card details for my employees.

Target Market(s)

Investors looking to make investment income through real estate

Industry/Entity Type

Real Estate

Contact Information for Business Card

Brent Kovalich
blank address, city, st, zip code
480-555-3174
brentkovalich@ridgeworthrentals.example
www.ridgeworthrentals.example

Font styles to use
Sans Serif

Requirements
Must have
• I would like the back of the card to have lines for info. example
• Met/Visited: Date:
• Interets:
Nice to have
• I want the cards color to match the logo background color. Font with details to be san serif and black. I want the card rectangular with square corners. Standard business card size. I would like to see cards designed with both images to see which i prefer more.

```html
<!DOCTYPE html>
<html lang="en">
<head>
<meta charset="utf-8">
<title>Ridgeworth Rentals – Business Card</title>
<link rel="stylesheet" href="https://fonts.googleapis.com/css2?family=Fira+Sans:wght@400;600;700&display=swap">
<style>
  :root {
    --teal: #1db9d8;
    --teal-deep: #0f8fb3;
    --ink: #0d0d0d;
    --paper: #ffffff;
    --stage: #e9ebec;
    --sea-top: #2ab3e0;
    --sea-bottom: #1a6e9a;
  }
  * { box-sizing: border-box; margin: 0; padding: 0; }
  html, body {
    width: 1200px; height: 873px; overflow: hidden;
    background: var(--stage);
    font-family: "Fira Sans", sans-serif;
  }
  .sheet {
    width: 1200px; height: 873px;
    display: flex; flex-direction: column; align-items: center; justify-content: center;
    gap: 46px;
  }
  .card {
    position: relative; width: 630px; height: 360px; overflow: hidden;
    box-shadow: 0 6px 18px rgba(0,0,0,.18);
  }
  .card-art { position: absolute; inset: 0; width: 100%; height: 100%; }

  /* Front */
  .card-front { background: var(--teal); }
  .brand {
    display: flex; align-items: center; gap: 8px;
  }
  .brand-mark { width: 14px; height: 14px; border-radius: 50%; background: currentColor; }
  .brand-name { font-weight: 600; font-size: 22px; letter-spacing: 3px; text-transform: uppercase; }
  .brand-motto { font-size: 9px; letter-spacing: .6px; margin-top: 4px; }
  .card-front .brand-block { position: absolute; left: 36px; top: 34px; color: var(--ink); }
  .holder { position: absolute; left: 36px; top: 126px; color: var(--ink); }
  .holder-name { font-size: 28px; font-weight: 400; }
  .holder-name strong { font-weight: 700; }
  .contact-list { list-style: none; margin-top: 14px; font-size: 14px; line-height: 1.55; }
  .contact-list li { display: flex; align-items: center; gap: 8px; }
  .contact-icon { width: 13px; height: 13px; flex: none; }
  .web-band {
    position: absolute; left: 0; right: 0; bottom: 0; height: 36px;
    background: var(--ink); color: var(--paper);
    font-size: 13px; font-weight: 600; letter-spacing: .4px;
    display: flex; align-items: center; padding-left: 36px;
  }

  /* Back */
  .card-back { background: var(--paper); }
  .card-back .brand-block {
    position: absolute; left: 32px; top: 140px; color: var(--teal); width: 200px;
  }
  .card-back .brand-name { font-size: 18px; letter-spacing: 2px; }
  .notes { position: absolute; left: 300px; right: 34px; top: 58px; color: var(--teal); }
  .note-row { display: flex; align-items: flex-end; gap: 10px; height: 48px; }
  .note-label { font-size: 17px; font-weight: 700; white-space: nowrap; }
  .note-rule {
    position: relative; flex: 1; height: 0; border-bottom: 1.5px solid var(--teal); margin-bottom: 5px;
  }
  .note-rule::before, .note-rule::after {
    content: ""; position: absolute; top: -4px; border: 4px solid transparent;
  }
  .note-rule::before { left: -2px; border-right: 7px solid var(--teal); border-left: 0; }
  .note-rule::after { right: -2px; border-left: 7px solid var(--teal); border-right: 0; }
</style>
</head>
<body>
<main class="sheet">

  <section class="card card-front" aria-label="Card front">
    <svg class="card-art" viewBox="0 0 630 360" aria-hidden="false">
      <defs>
        <linearGradient id="sea" x1="0" y1="0" x2="0" y2="1">
          <stop offset="0" stop-color="var(--sea-top)"/>
          <stop offset="1" stop-color="var(--sea-bottom)"/>
        </linearGradient>
      </defs>
      <path role="img" aria-label="Underwater photo of a manta ray gliding over a coral reef"
            d="M318,324 C350,324 340,118 410,108 L630,84 L630,324 Z"
            fill="url(#sea)" stroke="var(--ink)" stroke-width="4"/>
    </svg>

    <div class="brand-block">
      <div class="brand">
        <span class="brand-mark"></span>
        <span class="brand-name">Ridgeworth Rentals</span>
      </div>
      <p class="brand-motto">Clean, safe, and affordable housing</p>
    </div>

    <div class="holder">
      <h1 class="holder-name"><strong>Brent</strong> Kovalich</h1>
      <ul class="contact-list">
        <li>
          <svg class="contact-icon" viewBox="0 0 12 12"><rect width="12" height="12" rx="2" fill="var(--ink)"/><path d="M6 2.3a2.4 2.4 0 0 1 2.4 2.4C8.4 6.6 6 9.6 6 9.6S3.6 6.6 3.6 4.7A2.4 2.4 0 0 1 6 2.3z" fill="var(--teal)"/></svg>
          blank address, city, st, zip code
        </li>
        <li>
          <svg class="contact-icon" viewBox="0 0 12 12"><rect width="12" height="12" rx="2" fill="var(--ink)"/><path d="M3.6 2.6l1.4 0 .6 1.8-.9.7a5 5 0 0 0 2.2 2.2l.7-.9 1.8.6v1.4c-3.5.3-6.1-2.3-5.8-5.8z" fill="var(--teal)"/></svg>
          480-555-3174
        </li>
        <li>
          <svg class="contact-icon" viewBox="0 0 12 12"><rect width="12" height="12" rx="2" fill="var(--ink)"/><rect x="2.5" y="3.5" width="7" height="5" fill="none" stroke="var(--teal)"/><path d="M2.5 3.5 6 6.3 9.5 3.5" fill="none" stroke="var(--teal)"/></svg>
          brentkovalich@ridgeworthrentals.example
        </li>
      </ul>
    </div>

    <div class="web-band">www.ridgeworthrentals.example</div>
  </section>

  <section class="card card-back" aria-label="Card back">
    <svg class="card-art" viewBox="0 0 630 360" aria-hidden="true">
      <path d="M0,0 H262 C236,110 330,230 262,360 H0 Z" fill="var(--ink)"/>
    </svg>

    <div class="brand-block">
      <div class="brand">
        <span class="brand-mark"></span>
        <span class="brand-name">Ridgeworth Rentals</span>
      </div>
    </div>

    <div class="notes">
      <div class="note-row"><span class="note-label">Met/Visited:</span><span class="note-rule"></span></div>
      <div class="note-row"><span class="note-label">Date:</span><span class="note-rule"></span></div>
      <div class="note-row"><span class="note-label">Interets:</span><span class="note-rule"></span></div>
      <div class="note-row"><span class="note-rule"></span></div>
      <div class="note-row"><span class="note-rule"></span></div>
    </div>
  </section>

</main>
</body>
</html>
```